Professional Single Page Website Design for Tollbrook Advisory

Tollbrook Advisory is a new business consultancy specializing in providing expert services to small businesses, primarily in the brick-and-mortar retail and food service sectors. We offer a range of services including franchise development and launch, due diligence, and construction management.

Currently, we have a basic website set up at www.tollbrookadvisory.example, but we need a professional touch to enhance its design and functionality.

Project Requirements:
- Single Page Design: For now, we need a single page design that effectively showcases who we are, our services, and contact information.
- Future Expansion: The design should be flexible and scalable for future expansion to include additional pages like specific service offerings, about us, and a dedicated contact page.
- Design Aesthetic: We are looking for a modern yet professional design that aligns with our brand identity.
- Logo: We have a logo that we like, which was also sourced from Pixel Bazaar. The logo files are attached to this project brief.

Key Sections to Include:
- Hero Section: An engaging introduction to Tollbrook Advisory with a strong visual impact.
- About Us: A brief overview of who we are and our mission.
- Team: Section for the profiles of the two principals.
- Services: A clear and concise presentation of our services, including franchise development, due diligence, and construction management.
- Contact Information: Easy-to-find contact details, including a form for inquiries.
- Call to Action: Encouraging visitors to get in touch with us for consultations or further information.

Design Considerations:
- Ensure the design is responsive and mobile-friendly.
- Include high-quality images and icons that complement our services and industry.
- We do not need development services, this is only a design project.

```html
<!DOCTYPE html>
<html lang="en">
<head>
<meta charset="utf-8">
<title>Tollbrook Advisory</title>
<link rel="stylesheet" href="https://fonts.googleapis.com/css2?family=Poppins:wght@400;500;600;700&family=Montserrat:wght@400;500;600&family=Roboto:wght@400;500&display=swap">
<style>
:root{
  --green:#93c8b0;
  --green-soft:#e3faf0;
  --dark:#233039;
  --ink:#1e1e1e;
  --text:#3a3a3a;
  --field:#f0f0f0;
  --white:#ffffff;
}
*{margin:0;padding:0;box-sizing:border-box}
html,body{width:1200px;height:3845px;overflow:hidden}
body{position:relative;background:var(--white);font-family:"Roboto",sans-serif;color:var(--text)}
.abs{position:absolute}
.hero{left:0;top:0;width:1200px;height:693px;background:linear-gradient(100deg,#5a5550 0%,#7a6d60 40%,#a89580 70%,#6d7a62 100%)}
.hero-shade{left:0;top:0;width:1200px;height:693px;background:linear-gradient(90deg,rgba(20,20,20,.55),rgba(20,20,20,.1))}
.brand{left:112px;top:22px;display:flex;align-items:center;gap:12px;font-family:"Poppins",sans-serif;font-weight:600;font-size:24px;color:var(--white)}
.brand-dot{width:40px;height:40px;border-radius:50%;background:var(--green)}
.nav{top:36px;font-family:"Montserrat",sans-serif;font-size:15px;color:#2a2a2a}
.login{left:966px;top:25px;width:124px;height:39px;border-radius:20px;background:var(--dark);color:var(--white);font-family:"Montserrat",sans-serif;font-weight:600;font-size:13px;display:flex;align-items:center;justify-content:center;gap:8px}
.kicker{left:112px;top:175px;font-family:"Poppins",sans-serif;font-weight:500;font-size:27px;color:var(--green)}
.hero-title{left:110px;top:216px;width:560px;font-family:"Poppins",sans-serif;font-weight:700;font-size:50px;line-height:57px;color:var(--white)}
.btn{display:flex;align-items:center;justify-content:center;border-radius:28px;font-family:"Poppins",sans-serif;font-weight:600}
.btn-green{background:var(--green);color:var(--dark)}
.btn-dark{background:var(--dark);color:var(--white)}
.section-title{font-family:"Poppins",sans-serif;font-weight:600;font-size:36px;color:var(--ink)}
.about-text{left:109px;top:818px;width:540px;font-size:15px;line-height:30px;color:var(--text)}
.about-text p+p{margin-top:30px}
.divider{left:688px;top:843px;width:4px;height:287px;background:var(--green)}
.about-visual{left:720px;top:809px;width:390px;height:390px;border-radius:50%;background:var(--green)}
.services{left:3px;top:1355px;width:1197px;height:563px;background:var(--green-soft)}
.tab{top:1411px;height:33px;border-radius:17px;background:var(--green);color:var(--dark);font-family:"Poppins",sans-serif;font-weight:600;font-size:11px;display:flex;align-items:center;justify-content:center}
.tab.active{background:var(--dark);color:var(--white)}
.service-photo{left:112px;top:1482px;width:366px;height:357px}
.service-title{left:493px;top:1503px;font-family:"Poppins",sans-serif;font-weight:600;font-size:35px;color:var(--ink)}
.service-text{left:497px;top:1563px;width:590px;font-size:15.5px;line-height:33px;color:var(--text)}
.card{top:2157px;width:322px;height:398px;background:var(--white);box-shadow:0 4px 22px rgba(0,0,0,.08);text-align:center}
.avatar{position:absolute;left:81px;top:-80px;width:160px;height:160px;border-radius:50%;background:linear-gradient(160deg,#b9c7d3,#8a98a5)}
.card-name{margin-top:112px;font-family:"Poppins",sans-serif;font-weight:500;font-size:22px;color:var(--ink)}
.card-role{margin-top:4px;font-family:"Poppins",sans-serif;font-size:17px;color:var(--text)}
.card-links{margin-top:14px;display:flex;justify-content:center;gap:58px;font-family:"Poppins",sans-serif;font-size:16px;color:var(--text)}
.card-links span{display:flex;align-items:center;gap:8px}
.card-bio{margin:14px auto 0;width:296px;font-size:15px;line-height:28.5px;color:var(--text)}
.map{left:0;top:2664px;width:1200px;height:652px;background:linear-gradient(120deg,#e9ede9 0%,#f2f2ee 40%,#e6efe6 75%,#dfeee3 100%)}
.footer{left:0;top:3316px;width:1200px;height:529px;background:var(--dark)}
.contact-card{left:145px;top:2798px;width:389px;height:680px;background:var(--white);border-radius:6px;box-shadow:0 6px 24px rgba(0,0,0,.12)}
.contact-title{left:182px;top:2832px;font-family:"Poppins",sans-serif;font-weight:600;font-size:24px;color:var(--ink)}
.field{left:175px;width:328px;height:51px;background:var(--field);border-radius:4px;font-family:"Poppins",sans-serif;font-size:15px;color:#9a9a9a;padding:15px 28px}
.submit{left:173px;top:3390px;width:137px;height:58px;background:var(--green);color:var(--white);border-radius:3px;font-family:"Poppins",sans-serif;font-weight:600;font-size:14px;display:flex;align-items:center;justify-content:center}
.touch-card{left:554px;top:2897px;width:331px;height:327px;background:var(--white);border-radius:14px;box-shadow:0 6px 24px rgba(0,0,0,.1)}
.touch-title{left:578px;top:2924px;font-family:"Poppins",sans-serif;font-weight:600;font-size:24px;color:var(--ink);word-spacing:6px}
.touch-row{left:582px;font-size:15px;color:#2a2a2a;display:flex;gap:14px;line-height:26px}
.social{width:38px;height:38px;border-radius:50%}
.foot-brand{left:127px;top:3644px;font-family:"Poppins",sans-serif;font-weight:500;font-size:22px;color:var(--white);white-space:nowrap}
.foot-heading{top:3536px;font-family:"Poppins",sans-serif;font-weight:600;font-size:22px;color:var(--white)}
.foot-links{list-style:none;font-family:"Poppins",sans-serif;font-size:15px;color:var(--white);line-height:30px}
.foot-links li::before{content:"«";margin-right:10px}
.news-input{left:807px;top:3590px;width:278px;height:40px;border:1px solid #6b7780;border-radius:3px;font-family:"Poppins",sans-serif;font-size:14px;color:#8a949b;padding:9px 14px}
.news-btn{left:807px;top:3643px;width:278px;height:41px;background:var(--green);border-radius:3px;font-family:"Poppins",sans-serif;font-weight:600;font-size:15px;color:var(--dark);display:flex;align-items:center;justify-content:center}
.rule{left:400px;top:3750px;width:685px;height:1px;background:#3f4c55}
.copyright{left:0;top:3780px;width:1200px;text-align:center;font-family:"Poppins",sans-serif;font-size:15px;color:var(--white)}
</style>
</head>
<body>

<div class="abs hero" role="img" aria-label="Photo of a smiling consultant talking with a client at a table"></div>
<div class="abs hero-shade"></div>
<div class="abs brand"><span class="brand-dot"></span>Tollbrook Advisory</div>
<nav>
  <span class="abs nav" style="left:634px">About</span>
  <span class="abs nav" style="left:713px">Services</span>
  <span class="abs nav" style="left:805px">Team</span>
  <span class="abs nav" style="left:879px">Contact</span>
</nav>
<div class="abs login">
  <svg width="11" height="12" viewBox="0 0 11 12"><circle cx="5.5" cy="3" r="3" fill="#fff"/><path d="M0 12c0-4 2.5-5.5 5.5-5.5S11 8 11 12z" fill="#fff"/></svg>LOGIN
</div>
<div class="abs kicker">Tollbrook Advisory</div>
<h1 class="abs hero-title">An engaging introduction to Tollbrook Advisory with a strong visual impact</h1>
<div class="abs btn btn-green" style="left:112px;top:524px;width:200px;height:54px;font-size:19px">GET IN TOUCH</div>
<div class="abs btn btn-dark" style="left:334px;top:524px;width:232px;height:54px;font-size:19px">CONSULTATIONS</div>

<h2 class="abs section-title" style="left:109px;top:755px">About Us Tollbrook Advisory</h2>
<div class="abs about-text">
  <p>Welcome to Tollbrook Advisory, your trusted partner in navigating the complexities of the real estate and small business markets. Founded by industry veterans Adrian Velasco and Jonah Lim, we specialize in providing comprehensive services tailored to the unique needs of our clients. Whether you're a franchisee, a new restaurant owner, or a commercial real estate investor, our expertise in due diligence, construction management, and investment property evaluation ensures you make informed, strategic decisions.</p>
  <p>At Tollbrook Advisory, we are committed to your success. Our approach combines meticulous analysis, strategic insights, and personalized service to help you achieve your business goals. We pride ourselves on our ability to deliver results that exceed expectations, fostering long-term relationships built on trust and excellence.</p>
</div>
<div class="abs btn btn-dark" style="left:113px;top:1222px;width:148px;height:51px;font-size:17px">Learn More</div>
<div class="abs divider"></div>
<div class="abs about-visual"></div>

<section class="abs services"></section>
<div class="abs tab active" style="left:90px;width:209px">Franchise Development &amp; Launch</div>
<div class="abs tab" style="left:309px;width:103px">Due Diligence</div>
<div class="abs tab" style="left:419px;width:238px">Building &amp; Construction Management</div>
<div class="abs tab" style="left:667px;width:209px">Investment Property Evaluation</div>
<div class="abs tab" style="left:884px;width:225px">Market Analysis &amp; Feasibility Studies</div>
<svg class="abs service-photo" viewBox="0 0 366 357" role="img" aria-label="Photo of two colleagues working together at a laptop">
  <defs><linearGradient id="photoTone" x1="0" y1="0" x2="1" y2="1"><stop offset="0" stop-color="#8c98a3"/><stop offset="1" stop-color="#2c3a48"/></linearGradient></defs>
  <rect x="68" y="64" width="230" height="230" rx="48" transform="rotate(45 183 178)" fill="url(#photoTone)"/>
</svg>
<h3 class="abs service-title">Franchise Development &amp; Launch</h3>
<p class="abs service-text">At Tollbrook Advisory, our Franchise Development &amp; Launch service is designed to transform your successful business into a thriving franchise. We start by thoroughly evaluating your business model to determine its franchisability. Once confirmed, our team handles every aspect of the franchise setup, including legal documentation, branding, marketing strategies, operational guidelines, and franchisee recruitment.</p>
<div class="abs btn btn-dark" style="left:497px;top:1755px;width:155px;height:51px;font-size:16px">Read More</div>

<h2 class="abs section-title" style="left:0;width:1200px;text-align:center;top:1982px">Our Leadership Team</h2>
<article class="abs card" style="left:233px">
  <div class="avatar" role="img" aria-label="Portrait of Adrian Velasco"></div>
  <div class="card-name">Adrian Velasco</div>
  <div class="card-role">Principal</div>
  <div class="card-links">
    <span><svg width="14" height="14" viewBox="0 0 24 24"><path d="M6.6 10.8a15 15 0 006.6 6.6l2.2-2.2a1 1 0 011-.25 11.4 11.4 0 003.6.6 1 1 0 011 1V20a1 1 0 01-1 1A17 17 0 013 4a1 1 0 011-1h3.5a1 1 0 011 1 11.4 11.4 0 00.6 3.6 1 1 0 01-.25 1z" fill="#93c8b0"/></svg>Phone</span>
    <span><svg width="16" height="12" viewBox="0 0 16 12"><rect width="16" height="12" rx="1" fill="#93c8b0"/><path d="M1 1l7 5 7-5" stroke="#fff" stroke-width="1.4" fill="none"/></svg>Email</span>
  </div>
  <p class="card-bio">Adrian Velasco brings almost 20 years of rich experience as a real estate investor and a pivotal role at one of southern California's largest real estate management firms, where he...</p>
</article>
<article class="abs card" style="left:645px">
  <div class="avatar" role="img" aria-label="Portrait of Jonah Lim"></div>
  <div class="card-name">Jonah Lim</div>
  <div class="card-role">Principal</div>
  <div class="card-links">
    <span><svg width="14" height="14" viewBox="0 0 24 24"><path d="M6.6 10.8a15 15 0 006.6 6.6l2.2-2.2a1 1 0 011-.25 11.4 11.4 0 003.6.6 1 1 0 011 1V20a1 1 0 01-1 1A17 17 0 013 4a1 1 0 011-1h3.5a1 1 0 011 1 11.4 11.4 0 00.6 3.6 1 1 0 01-.25 1z" fill="#93c8b0"/></svg>Phone</span>
    <span><svg width="16" height="12" viewBox="0 0 16 12"><rect width="16" height="12" rx="1" fill="#93c8b0"/><path d="M1 1l7 5 7-5" stroke="#fff" stroke-width="1.4" fill="none"/></svg>Email</span>
  </div>
  <p class="card-bio">Jonah Lim is a seasoned real estate expert with extensive experience in project and construction management, and a licensed real estate agent in California. Fluent in both English and Korean,...</p>
</article>

<div class="abs map" role="img" aria-label="Street map of the office surroundings"></div>
<footer class="abs footer"></footer>

<div class="abs contact-card"></div>
<h3 class="abs contact-title">CONTACT US!</h3>
<div class="abs field" style="top:2897px">First Name</div>
<div class="abs field" style="top:2963px">Last Name</div>
<div class="abs field" style="top:3030px">Company</div>
<div class="abs field" style="top:3097px">Phone</div>
<div class="abs field" style="top:3160px">Email</div>
<div class="abs field" style="top:3227px;height:140px">Messages</div>
<div class="abs submit">SUBMIT</div>

<div class="abs touch-card"></div>
<h3 class="abs touch-title">GET IN TOUCH</h3>
<div class="abs touch-row" style="top:2992px">
  <svg width="14" height="18" viewBox="0 0 14 18" style="margin-top:4px"><path d="M7 0a7 7 0 017 7c0 5-7 11-7 11S0 12 0 7a7 7 0 017-7z" fill="#93c8b0"/><circle cx="7" cy="7" r="2.5" fill="#fff"/></svg>
  <span>855 Tollbrook Way<br>Lorem ipsum dolor sit amet,</span>
</div>
<div class="abs touch-row" style="top:3056px">
  <svg width="18" height="18" viewBox="0 0 24 24" style="margin-top:3px"><path d="M6.6 10.8a15 15 0 006.6 6.6l2.2-2.2a1 1 0 011-.25 11.4 11.4 0 003.6.6 1 1 0 011 1V20a1 1 0 01-1 1A17 17 0 013 4a1 1 0 011-1h3.5a1 1 0 011 1 11.4 11.4 0 00.6 3.6 1 1 0 01-.25 1z" fill="#93c8b0"/></svg>
  <span style="font-size:16px">555-010-0142</span>
</div>
<div class="abs touch-row" style="top:3099px">
  <svg width="18" height="14" viewBox="0 0 16 12" style="margin-top:6px"><rect width="16" height="12" rx="1" fill="#93c8b0"/><path d="M1 1l7 5 7-5" stroke="#fff" stroke-width="1.4" fill="none"/></svg>
  <span>Email: info@tollbrookadvisory.example</span>
</div>
<div class="abs social" style="left:582px;top:3156px;background:var(--green)"></div>
<div class="abs social" style="left:629px;top:3156px;border:2px solid var(--green)"></div>

<div class="abs" style="left:199px;top:3530px;width:56px;height:56px;border-radius:50%;background:var(--green)"></div>
<div class="abs foot-brand">Tollbrook Advisory</div>
<div class="abs" style="left:209px;top:3691px;width:25px;height:25px;border-radius:50%;background:var(--green)"></div>
<div class="abs" style="left:243px;top:3691px;width:25px;height:25px;border-radius:50%;border:2px solid var(--white)"></div>

<h4 class="abs foot-heading" style="left:407px">Quick Link</h4>
<ul class="abs foot-links" style="left:404px;top:3581px"><li>About</li><li>Team</li><li>Services</li><li>Contact</li></ul>
<h4 class="abs foot-heading" style="left:593px">Help Link</h4>
<ul class="abs foot-links" style="left:593px;top:3581px"><li>Terms&amp;conditions</li><li>Privacy Policy</li><li>About Us</li><li>Support</li></ul>
<h4 class="abs foot-heading" style="left:806px">Get Our Newsletter</h4>
<div class="abs news-input">Enter Your Email</div>
<div class="abs news-btn">Subscribe Now</div>
<div class="abs rule"></div>
<p class="abs copyright">©Copyrights 2024 Tollbrook Advisory | &nbsp; All Rights Reserved</p>

</body>
</html>
```